Global (re)insurance broker needs a business card design

We need a classic business card for our company that is headquartered in SG, with offices in Malaysia and Dubai. We specialise in insurance and reinsurance broking and consultancy for our global clients.

```html
<!DOCTYPE html>
<html lang="en">
<head>
<meta charset="utf-8">
<title>Meridane — Business Card</title>
<link rel="stylesheet" href="https://fonts.googleapis.com/css2?family=Arimo:wght@400;700&display=swap">
<style>
  :root {
    --backdrop: #e4e4e4;
    --card-dark: #333333;
    --card-blue: #25479a;
    --card-blue-deep: #1c3a86;
    --accent-blue: #2f4fb0;
    --mint: #c9e4c4;
    --text-light: #f2f2f2;
    --rule: #9a9a9a;
  }
  * { box-sizing: border-box; margin: 0; padding: 0; }
  html, body { width: 1200px; height: 802px; overflow: hidden; }
  body {
    background: var(--backdrop);
    font-family: "Arimo", Arial, sans-serif;
    display: flex;
    align-items: center;
    justify-content: center;
    gap: 56px;
  }
  .card {
    width: 518px;
    height: 296px;
    position: relative;
    overflow: hidden;
    box-shadow: 0 10px 24px rgba(0,0,0,0.18);
  }

  /* Contact side */
  .card--contact { background: var(--card-dark); border-bottom: 3px solid var(--accent-blue); }
  .card--contact .wordmark {
    position: absolute;
    left: 40px;
    top: 128px;
    font-weight: 700;
    font-size: 34px;
    letter-spacing: 1px;
    color: var(--mint);
  }
  .card--contact .divider {
    position: absolute;
    left: 262px;
    top: 70px;
    width: 1px;
    height: 156px;
    background: var(--rule);
  }
  .details {
    position: absolute;
    left: 284px;
    top: 74px;
    color: var(--text-light);
    font-size: 13px;
    line-height: 1.32;
  }
  .details .person-name {
    color: var(--accent-blue);
    font-weight: 700;
    font-size: 16px;
    letter-spacing: 0.5px;
  }
  .details .person-role { margin-bottom: 8px; }
  .details .address { margin-bottom: 10px; }
  .contact-line { display: flex; align-items: center; gap: 7px; }
  .contact-line svg { width: 11px; height: 11px; flex: none; }

  /* Brand side */
  .card--brand { background: var(--card-blue); }
  .card--brand .decor {
    position: absolute;
    right: -60px;
    top: -40px;
    width: 380px;
    height: 380px;
    border-radius: 50%;
    background: radial-gradient(circle at 40% 40%, #2b51ab 0%, var(--card-blue-deep) 70%);
    opacity: 0.85;
  }
  .card--brand .wordmark {
    position: absolute;
    left: 40px;
    bottom: 52px;
    font-weight: 700;
    font-size: 36px;
    letter-spacing: 1px;
    color: #ffffff;
  }
</style>
</head>
<body>
  <section class="card card--contact">
    <div class="wordmark">MERIDANE</div>
    <div class="divider"></div>
    <div class="details">
      <div class="person-name">JONATHAN SMITH</div>
      <div class="person-role">Manager</div>
      <div class="address">Your Address, City<br>State, Zip 0000</div>
      <div class="contact-line">
        <svg viewBox="0 0 12 12"><path d="M2.5 1h2l1 3-1.3 1a6 6 0 0 0 2.8 2.8L8 6.5l3 1v2A1.5 1.5 0 0 1 9.5 11 8.5 8.5 0 0 1 1 2.5 1.5 1.5 0 0 1 2.5 1z" fill="#f2f2f2"/></svg>
        <span>123-456-2100</span>
      </div>
      <div class="contact-line">
        <svg viewBox="0 0 12 12"><rect x="1" y="2.5" width="10" height="7" fill="none" stroke="#f2f2f2" stroke-width="1"/><path d="M1 2.5l5 4 5-4" fill="none" stroke="#f2f2f2" stroke-width="1"/></svg>
        <span>youremail@mailbox.com</span>
      </div>
      <div class="contact-line">
        <svg viewBox="0 0 12 12"><circle cx="6" cy="6" r="5" fill="none" stroke="#f2f2f2" stroke-width="1"/><ellipse cx="6" cy="6" rx="2.2" ry="5" fill="none" stroke="#f2f2f2" stroke-width="0.8"/><path d="M1 6h10" stroke="#f2f2f2" stroke-width="0.8"/></svg>
        <span>www.yourwebsite.com</span>
      </div>
    </div>
  </section>

  <section class="card card--brand">
    <div class="decor" role="img" aria-label="Soft blue background shape"></div>
    <div class="wordmark">MERIDANE</div>
  </section>
</body>
</html>
```